Education Certificate

We need a modern yet professional Certificate for those who successfully pass / complete our online Training course.

There are various courses but ONE certificate design required.

the certificate needs to look extremely professional and of value.

```html
<!DOCTYPE html>
<html lang="en">
<head>
<meta charset="utf-8">
<title>Certificate of Completion</title>
<link rel="stylesheet" href="https://fonts.googleapis.com/css2?family=Arimo:ital,wght@0,400;0,700;1,700&family=Open+Sans:wght@700&family=Playfair+Display:wght@900&display=swap">
<style>
  :root {
    --navy: #1f2f6b;
    --gold: #ffd200;
    --paper: #ffffff;
    --seal-edge: #9a9a9a;
  }
  * { margin: 0; padding: 0; box-sizing: border-box; }
  html, body { width: 1200px; height: 848px; overflow: hidden; background: var(--paper); }
  .certificate {
    position: relative; width: 1200px; height: 848px;
    background: var(--paper); color: var(--navy);
    font-family: "Arimo", Arial, sans-serif;
  }
  .brand {
    position: absolute; left: 86px; top: 92px; width: 180px;
    display: flex; align-items: flex-start; gap: 8px;
    font-family: "Arimo", Arial, sans-serif; font-weight: 700;
    font-size: 17px; line-height: 21px; color: var(--navy);
  }
  .brand-mark { width: 14px; height: 14px; background: var(--gold); flex: none; margin-top: 4px; }
  .divider { position: absolute; left: 282px; top: 109px; width: 2px; height: 77px; background: var(--navy); }
  .title {
    position: absolute; left: 305px; top: 86px;
    font-family: "Playfair Display", Georgia, serif; font-weight: 900;
    font-size: 74px; line-height: 1; color: var(--navy); letter-spacing: 0.5px;
  }
  .subtitle {
    position: absolute; left: 308px; top: 164px;
    font-family: "Playfair Display", Georgia, serif; font-weight: 900;
    font-size: 27px; line-height: 1; color: var(--navy);
  }
  .recipient {
    position: absolute; left: 83px; top: 283px;
    font-family: "Open Sans", Arial, sans-serif; font-weight: 700;
    font-size: 68px; line-height: 1; color: var(--gold); letter-spacing: -0.5px;
  }
  .lead { position: absolute; left: 87px; top: 357px; font-size: 20px; }
  .course-name { position: absolute; left: 86px; top: 405px; font-size: 19.5px; font-weight: 700; letter-spacing: 0.2px; }
  .course-text { position: absolute; left: 86px; width: 640px; font-size: 16.8px; line-height: 19px; }
  .course-text.first { top: 440px; }
  .course-text.second { top: 497px; }
  .date { position: absolute; left: 86px; top: 583px; font-size: 22px; }
  .signature {
    position: absolute; left: 92px; top: 660px; width: 160px; height: 56px;
    background: linear-gradient(90deg, rgba(31,47,107,0.06), rgba(31,47,107,0.12));
    border-radius: 4px;
  }
  .signature-line { position: absolute; left: 86px; top: 721px; width: 194px; height: 1px; background: var(--navy); }
  .signatory { position: absolute; left: 131px; top: 727px; font-size: 16px; font-weight: 700; font-style: italic; }
  .ribbon { position: absolute; left: 945px; top: 0; width: 170px; height: 652px; }
  .seal { position: absolute; left: 895px; top: 205px; width: 272px; height: 256px; }
</style>
</head>
<body>
<main class="certificate">
  <div class="brand"><span class="brand-mark"></span><span>Global Service Excellence Academy</span></div>
  <div class="divider"></div>
  <h1 class="title">Certificate</h1>
  <p class="subtitle">of Completion</p>

  <p class="recipient">Amelia Brooks</p>
  <p class="lead">has completed the following course:</p>
  <h2 class="course-name">DIGITAL SERVICE EXPERIENCE FRAMEWORK DSXF2024</h2>
  <p class="course-text first">DSXF2024 reflects the increased international growth in scale, reach and scope of digital transformation and services delivered through Digital Channels.</p>
  <p class="course-text second">The primary aim of the DSXF2024 Framework is to motivate organisations to focus their attention on the Digital Customer Experience through the delivery of service excellence techniques</p>
  <p class="date">on March 20, 2024</p>

  <div class="signature" role="img" aria-label="Handwritten signature of the chief executive"></div>
  <div class="signature-line"></div>
  <p class="signatory">CEO, gsea</p>

  <svg class="ribbon" viewBox="0 0 170 652" aria-hidden="true">
    <polygon points="0,0 170,0 170,652 85,586 0,652" fill="var(--navy)"/>
  </svg>

  <svg class="seal" viewBox="0 0 272 256" aria-hidden="true">
    <defs>
      <filter id="seal-shadow" x="-20%" y="-20%" width="140%" height="140%">
        <feDropShadow dx="0" dy="0" stdDeviation="10" flood-color="#000" flood-opacity="0.18"/>
      </filter>
    </defs>
    <circle cx="136" cy="128" r="122" fill="var(--navy)" stroke="var(--seal-edge)" stroke-width="1.5" filter="url(#seal-shadow)"/>
    <circle cx="136" cy="128" r="93" fill="none" stroke="var(--paper)" stroke-width="5"/>
    <circle cx="135" cy="128" r="37" fill="var(--paper)"/>
    <polyline points="120,129 131,139 151,121" fill="none" stroke="#f0cf30" stroke-width="6" stroke-linecap="round" stroke-linejoin="round"/>
  </svg>
</main>
</body>
</html>
```